A new presentation to our clients

we are a Real Estate agency, our website is www.lumibrasa.com and it’s time to have a new, fashion and remarcable Business Card. we want to differentiate ourselves from other companies so we want a business card that differentiates us. we want the business card to impact our customers. in the competitive market that we have today, we have to be different and it is this difference that we seek

Target Market(s)

Real Estate Clients

Contact Information for Business Card

We search a totaly diferent card from the usual

Font styles to use
Sans Serif

Colors
e34197

Requirements
Must have
• Logo, adress, phone contact, e-mail, photo, and our website
Nice to have
• We would like to see a modern business card
Should not have
• Houses or building draws

```html
<!DOCTYPE html>
<html lang="en">
<head>
<meta charset="utf-8">
<title>Lumibrasa Business Card</title>
<link href="https://fonts.googleapis.com/css2?family=Lato:wght@400;700&display=swap" rel="stylesheet">
<style>
  :root {
    --page-bg: #2a2a2d;
    --card-bg: #45474f;
    --accent: #e32f7f;
    --text-light: #f2f2f4;
  }
  html, body {
    margin: 0;
    padding: 0;
    width: 1200px;
    height: 1200px;
    overflow: hidden;
    background: var(--page-bg);
    font-family: "Lato", sans-serif;
  }
  .card {
    position: absolute;
    left: 140px;
    width: 920px;
    height: 525px;
    background: var(--card-bg);
    border-radius: 32px;
    overflow: hidden;
  }
  .card--front { top: 48px; }
  .card--back { top: 639px; }
  .brand-name {
    position: absolute;
    margin: 0;
    font-weight: 700;
    font-size: 120px;
    line-height: 1;
    color: var(--accent);
    letter-spacing: 1px;
  }
  .card--front .brand-name { left: 58px; top: 46px; }
  .card--back .brand-name { right: 60px; top: 348px; }
  .holder {
    position: absolute;
    right: 68px;
    top: 280px;
    margin: 0;
    font-size: 34px;
    font-weight: 400;
    color: var(--text-light);
    line-height: 1;
  }
  .holder .surname { color: var(--accent); }
  .rule {
    position: absolute;
    left: 60px;
    top: 335px;
    width: 630px;
    height: 2px;
    background: var(--accent);
  }
  .role {
    position: absolute;
    right: 68px;
    top: 323px;
    margin: 0;
    font-size: 24px;
    color: var(--accent);
    line-height: 1;
  }
  .contacts {
    position: absolute;
    right: 60px;
    top: 372px;
    margin: 0;
    padding: 0;
    list-style: none;
  }
  .contacts li {
    display: flex;
    justify-content: flex-end;
    align-items: center;
    height: 28px;
    margin-bottom: 2px;
    font-size: 21px;
    color: var(--text-light);
  }
  .contacts .highlight { color: var(--accent); }
  .contacts svg {
    width: 20px;
    height: 20px;
    margin-left: 22px;
    fill: var(--accent);
  }
  .address {
    position: absolute;
    left: 60px;
    top: 441px;
    margin: 0;
    font-size: 22px;
    font-style: normal;
    line-height: 23px;
    color: var(--text-light);
  }
</style>
</head>
<body>
  <section class="card card--front">
    <h1 class="brand-name">Lumibrasa</h1>
    <h2 class="holder">RAFA <span class="surname">MORENO</span></h2>
    <div class="rule"></div>
    <p class="role">CEO/manager</p>
    <ul class="contacts">
      <li>+351 - 218 - 4470
        <svg viewBox="0 0 20 20"><path d="M5 1h10a1 1 0 0 1 1 1v16a1 1 0 0 1-1 1H5a1 1 0 0 1-1-1V2a1 1 0 0 1 1-1zm1 2v12h8V3zm4 13a1 1 0 1 0 0 2 1 1 0 0 0 0-2z"/></svg>
      </li>
      <li>+351 - 218 - 4471
        <svg viewBox="0 0 20 20"><path d="M2 6c0-2 3-3 8-3s8 1 8 3v2h-4V6.5H6V8H2zm3 3h10l2 8H3zm5 2a2 2 0 1 0 0 4 2 2 0 0 0 0-4z"/></svg>
      </li>
      <li>hello@lumibrasa.com
        <svg viewBox="0 0 20 20"><path d="M1 4h18v12H1zm2 2v.5l7 5 7-5V6l-7 5z"/></svg>
      </li>
      <li>www.<span class="highlight">lumibrasa</span>.com
        <svg viewBox="0 0 20 20"><path d="M10 1a9 9 0 1 0 0 18 9 9 0 0 0 0-18zm0 1.6c.9 1 1.6 2.6 1.9 4.4H8.1c.3-1.8 1-3.4 1.9-4.4zM3 9h3.3a14 14 0 0 0 0 2H3a7 7 0 0 1 0-2zm5 0h4a12 12 0 0 1 0 2H8a12 12 0 0 1 0-2zm5.7 0H17a7 7 0 0 1 0 2h-3.3a14 14 0 0 0 0-2zM8.1 13h3.8c-.3 1.8-1 3.4-1.9 4.4-.9-1-1.6-2.6-1.9-4.4zM4 7a7 7 0 0 1 3-3.4A10 10 0 0 0 6.4 7zm9.6 0A10 10 0 0 0 13 3.6 7 7 0 0 1 16 7zM4 13h2.4c.1 1.2.3 2.3.6 3.4A7 7 0 0 1 4 13zm9.6 0H16a7 7 0 0 1-3 3.4c.3-1.1.5-2.2.6-3.4z"/></svg>
      </li>
    </ul>
    <address class="address">Harbor Lane 41870<br>Marisol Avenue Costa Verde</address>
  </section>
  <section class="card card--back">
    <p class="brand-name">Lumibrasa</p>
  </section>
</body>
</html>
```